SkyvornQ Business Cards and Stationary Design

Need a design for our business cards and stationary. I want to carry on the theme of the logo. I want the business cards to have a design on the back. I would like the business cards and the stationary to carry the same theme, design scheme, and branding

Target Market(s)

Airlines and Maintenance Facilities

Industry/Entity Type

Aviation

Contact Information for Business Card

Name
Position Title
Address: 4827 Trellis Hollow Road, Veldmoor, Wessland, 34951
Office Number
Mobile Number
Email
Website

Font styles to use
Serif
Sans Serif

Colors

Designer to choose colors to be used in the design.

```html
<!DOCTYPE html>
<html lang="en">
<head>
<meta charset="utf-8">
<title>SkyvornQ Business Cards</title>
<link rel="stylesheet" href="https://fonts.googleapis.com/css2?family=Roboto:wght@400;500;700&display=swap">
<style>
  :root {
    --navy: #14284f;
    --sky: #2a9ad8;
    --white: #ffffff;
    --stage: #2b2b2b;
  }
  * { box-sizing: border-box; margin: 0; padding: 0; }
  html, body { width: 1200px; height: 930px; overflow: hidden; }
  body {
    background: var(--stage);
    font-family: "Roboto", Arial, sans-serif;
    position: relative;
  }
  .card {
    position: absolute;
    width: 540px;
    height: 310px;
    border-radius: 16px;
    overflow: hidden;
    background: var(--navy);
    box-shadow: 0 14px 30px rgba(0,0,0,0.45);
  }
  .card-back { left: 90px; top: 90px; }
  .card-front { left: 570px; top: 520px; }

  .brand {
    display: flex;
    align-items: center;
    gap: 14px;
  }
  .brand-mark {
    width: 40px; height: 40px;
    border-radius: 50%;
    border: 5px solid currentColor;
    flex: none;
  }
  .brand-name {
    font-weight: 700;
    letter-spacing: 0.22em;
    font-size: 38px;
    line-height: 1;
    white-space: nowrap;
  }

  .card-back .brand {
    position: absolute;
    left: 0; right: 0; top: 110px;
    justify-content: center;
    color: var(--white);
  }
  .card-back .web {
    position: absolute;
    left: 0; right: 0; bottom: 44px;
    text-align: center;
    color: var(--white);
    font-size: 13px;
    letter-spacing: 0.02em;
  }
  .card-back .web b { font-weight: 700; }

  .front-art { position: absolute; inset: 0; }
  .card-front .brand {
    position: absolute;
    right: 28px; top: 92px;
    gap: 12px;
    color: var(--navy);
  }
  .card-front .brand-name { font-size: 28px; }
  .card-front .brand-mark { width: 30px; height: 30px; border-width: 4px; border-color: var(--sky); }

  .contact {
    position: absolute;
    left: 34px; bottom: 22px;
    color: var(--white);
    font-size: 12.5px;
    line-height: 1.45;
  }
  .contact .person { font-size: 19px; font-weight: 500; letter-spacing: 0.03em; text-transform: uppercase; }
  .contact .role { font-size: 13px; margin-bottom: 8px; }
  .contact .address { margin-bottom: 6px; }
  .contact .line { display: flex; align-items: center; gap: 8px; }
  .contact .line svg { width: 11px; height: 11px; flex: none; }
  .contact .line b { font-weight: 700; }
</style>
</head>
<body>

  <section class="card card-back" aria-label="Business card back">
    <div class="brand">
      <span class="brand-mark"></span>
      <span class="brand-name">SKYVORNQ</span>
    </div>
    <p class="web">www.<b>skyvornq</b>.com</p>
  </section>

  <section class="card card-front" aria-label="Business card front">
    <svg class="front-art" viewBox="0 0 540 310" preserveAspectRatio="none" aria-hidden="true">
      <path d="M206,0 C232,156 318,266 540,242" fill="none" stroke="var(--sky)" stroke-width="5"/>
      <path d="M218,0 L540,0 L540,236 C330,258 244,150 218,0 Z" fill="var(--white)"/>
    </svg>

    <div class="brand">
      <span class="brand-mark"></span>
      <span class="brand-name">SKYVORNQ</span>
    </div>

    <div class="contact">
      <p class="person">Dorian Vell</p>
      <p class="role">Director</p>
      <p class="address">4827 Trellis Hollow Road,<br>Veldmoor, Wessland, 34951</p>
      <p class="line">
        <svg viewBox="0 0 12 12"><path d="M3 1 L5 3.5 L4 5 Q5 7 7 8 L8.5 7 L11 9 L10 11 Q4 11 1 3 Z" fill="currentColor"/></svg>
        <span>555-218-7730</span>
      </p>
      <p class="line">
        <svg viewBox="0 0 12 12"><rect x="1" y="2.5" width="10" height="7" fill="none" stroke="currentColor" stroke-width="1.2"/><path d="M1 2.5 L6 6.5 L11 2.5" fill="none" stroke="currentColor" stroke-width="1.2"/></svg>
        <span>info@skyvornq.com</span>
      </p>
      <p class="line">
        <svg viewBox="0 0 12 12"><circle cx="6" cy="6" r="5" fill="none" stroke="currentColor" stroke-width="1.2"/><path d="M1 6 H11 M6 1 Q3 6 6 11 Q9 6 6 1" fill="none" stroke="currentColor" stroke-width="1"/></svg>
        <span>www.<b>skyvornq</b>.com</span>
      </p>
    </div>
  </section>

</body>
</html>
```